Ashwell Court Apartments
stationary
Project: Ashwell Court Apartments
Ashwell Court Apartments - Real Estate
Creative Brief
Traditional
Daniel Kessing
2430 Ashwell Court Houston TX 77091
dpkessing@mailvora.net

```html
<!DOCTYPE html>
<html lang="en">
<head>
<meta charset="utf-8">
<title>Ashwell Court Apartments – Business Card</title>
<link href="https://fonts.googleapis.com/css2?family=Cinzel:wght@500&family=Tinos&display=swap" rel="stylesheet">
<style>
  :root {
    --stage: #e4e4e2;
    --brand-green: #2f8f3f;
    --card-white: #ffffff;
    --ink-grey: #4a4a4a;
    --rule-grey: #b9b9b9;
  }
  html, body {
    margin: 0;
    width: 1200px;
    height: 871px;
    overflow: hidden;
    background: var(--stage);
  }
  .canvas {
    position: relative;
    width: 1200px;
    height: 871px;
  }
  .card {
    position: absolute;
    top: 285px;
    width: 520px;
    height: 300px;
    border-radius: 6px;
    overflow: hidden;
    box-shadow: 0 4px 14px rgba(0,0,0,.14);
  }
  .card--back { left: 60px; background: var(--brand-green); }
  .card--front { left: 620px; background: var(--card-white); }

  .wordmark {
    position: absolute;
    left: 0; right: 0;
    display: flex;
    flex-direction: column;
    align-items: center;
    font-family: "Cinzel", serif;
    font-weight: 500;
    text-align: center;
  }
  .wordmark__square {
    width: 34px; height: 34px;
    margin-bottom: 12px;
  }
  .wordmark__name {
    font-size: 25px;
    line-height: 1.15;
    letter-spacing: .5px;
  }
  .card--back .wordmark { top: 88px; color: var(--card-white); }
  .card--back .wordmark__square { background: var(--card-white); }
  .card--front .wordmark { top: 40px; color: var(--brand-green); }
  .card--front .wordmark__square { background: var(--brand-green); }

  .edge-tab {
    position: absolute;
    width: 16px;
    height: 122px;
    background: var(--brand-green);
  }
  .edge-tab--left { left: 0; top: 148px; border-radius: 0 12px 12px 0; }
  .edge-tab--right { right: 0; top: 30px; border-radius: 12px 0 0 12px; }

  .holder-name {
    position: absolute;
    left: 40px;
    top: 244px;
    font-family: "Cinzel", serif;
    font-weight: 500;
    font-size: 17px;
    color: var(--brand-green);
    letter-spacing: .3px;
  }
  .divider {
    position: absolute;
    left: 262px;
    top: 176px;
    width: 1px;
    height: 96px;
    background: var(--rule-grey);
  }
  .contact {
    position: absolute;
    left: 276px;
    top: 178px;
    font-family: "Tinos", serif;
    font-size: 12.5px;
    line-height: 17px;
    color: var(--ink-grey);
  }
  .contact__address { margin: 0 0 6px; }
  .contact__line {
    display: flex;
    align-items: center;
    gap: 6px;
  }
  .contact__icon { width: 10px; height: 10px; fill: var(--brand-green); }
</style>
</head>
<body>
<main class="canvas">
  <section class="card card--back" aria-label="Card back">
    <div class="wordmark">
      <span class="wordmark__square"></span>
      <span class="wordmark__name">Ashwell Court<br>Apartments</span>
    </div>
  </section>

  <section class="card card--front" aria-label="Card front">
    <span class="edge-tab edge-tab--left"></span>
    <span class="edge-tab edge-tab--right"></span>

    <div class="wordmark">
      <span class="wordmark__square"></span>
      <span class="wordmark__name">Ashwell Court<br>Apartments</span>
    </div>

    <div class="holder-name">Daniel Kessing</div>
    <span class="divider"></span>

    <div class="contact">
      <p class="contact__address">2430 Ashwell Court<br>Houston TX 77091</p>
      <div class="contact__line">
        <svg class="contact__icon" viewBox="0 0 10 10" aria-hidden="true"><path d="M2 0.5l2 2.2-1 1.2c.6 1.3 1.6 2.3 2.9 2.9l1.2-1 2.2 2-1.3 1.7C4.3 9.3.7 5.7.3 1.8z"/></svg>
        <span>713-555-0184</span>
      </div>
      <div class="contact__line">
        <svg class="contact__icon" viewBox="0 0 10 10" aria-hidden="true"><path d="M0 2h10v6H0z M0.6 2.4L5 5.6 9.4 2.4" fill="none" stroke="#2f8f3f" stroke-width="1.2"/></svg>
        <span>dpkessing@mailvora.net</span>
      </div>
    </div>
  </section>
</main>
</body>
</html>
```